SaaS Early tech startup business card design

Unique design for experience ecommerce platform company. the business cards will be used by executive members. conformance with color code is required.

```html
<!DOCTYPE html>
<html lang="en">
<head>
<meta charset="utf-8">
<title>Kovlo – Business Card</title>
<link rel="stylesheet" href="https://fonts.googleapis.com/css2?family=Lato:wght@400;700;900&family=Montserrat:wght@600&display=swap">
<style>
  :root {
    --teal: #00b09b;
    --teal-light: #33c1ac;
    --navy: #0b6790;
    --ink: #1d2a30;
    --paper: #ffffff;
    --stage: #e9eceb;
  }
  * { box-sizing: border-box; margin: 0; padding: 0; }
  html, body { width: 1200px; height: 900px; overflow: hidden; }
  body {
    background: var(--stage);
    font-family: "Lato", sans-serif;
    display: flex;
    flex-direction: column;
    align-items: center;
    justify-content: center;
    gap: 34px;
  }
  .card {
    position: relative;
    width: 700px;
    height: 400px;
    overflow: hidden;
    box-shadow: 0 6px 18px rgba(0,0,0,0.18);
  }

  /* Back side */
  .card--back { background: var(--teal); display: flex; align-items: center; justify-content: center; }
  .wordmark {
    font-family: "Lato", sans-serif;
    font-weight: 900;
    color: var(--navy);
    letter-spacing: 2px;
    line-height: 1;
  }
  .card--back .wordmark { font-size: 130px; }

  /* Front side */
  .card--front { background: var(--paper); }
  .card__wave { position: absolute; inset: 0; width: 100%; height: 100%; }
  .holder { position: absolute; left: 58px; top: 78px; }
  .holder__name {
    font-family: "Montserrat", sans-serif;
    font-weight: 600;
    font-size: 25px;
    color: var(--teal);
    letter-spacing: 0.5px;
    text-transform: uppercase;
  }
  .holder__title { font-size: 17px; color: var(--ink); margin-top: 2px; }
  .card--front .wordmark { position: absolute; right: 52px; top: 70px; font-size: 92px; }

  .contact { position: absolute; left: 82px; top: 186px; font-size: 17px; color: var(--ink); }
  .contact__row { display: flex; align-items: center; gap: 10px; height: 26px; }
  .contact__icon { width: 20px; height: 20px; flex: none; }
  .contact__address { margin-top: 18px; padding-left: 30px; line-height: 1.4; }

  .website {
    position: absolute; right: 40px; bottom: 58px;
    font-size: 16px; color: var(--paper); letter-spacing: 0.5px;
  }
</style>
</head>
<body>

  <section class="card card--back" aria-label="Card back">
    <span class="wordmark">Kovlo</span>
  </section>

  <section class="card card--front" aria-label="Card front">
    <svg class="card__wave" viewBox="0 0 700 400" preserveAspectRatio="none" aria-hidden="true">
      <path d="M0,345 C260,345 420,300 560,232 C620,203 665,188 700,184 L700,400 L0,400 Z" fill="var(--teal)"/>
      <path d="M0,318 C230,318 420,285 530,222 C430,292 240,336 0,336 Z" fill="var(--navy)"/>
      <path d="M0,338 C240,338 430,296 532,226 C440,300 250,343 0,343 Z" fill="var(--paper)"/>
    </svg>

    <div class="holder">
      <h1 class="holder__name">Daniel Moreau</h1>
      <p class="holder__title">Managing Director</p>
    </div>

    <span class="wordmark">Kovlo</span>

    <div class="contact">
      <div class="contact__row">
        <svg class="contact__icon" viewBox="0 0 24 24" aria-hidden="true">
          <path d="M6.6 10.8a15.1 15.1 0 0 0 6.6 6.6l2.2-2.2a1 1 0 0 1 1-.25 11.4 11.4 0 0 0 3.6.57 1 1 0 0 1 1 1V20a1 1 0 0 1-1 1A17 17 0 0 1 3 4a1 1 0 0 1 1-1h3.5a1 1 0 0 1 1 1c0 1.25.2 2.45.57 3.57a1 1 0 0 1-.25 1z" fill="var(--teal)"/>
        </svg>
        <span>044-987 654 321</span>
      </div>
      <div class="contact__row">
        <svg class="contact__icon" viewBox="0 0 24 24" aria-hidden="true">
          <rect x="2" y="5" width="20" height="14" fill="var(--teal)"/>
          <path d="M2 5 L12 13 L22 5" fill="none" stroke="var(--paper)" stroke-width="1.6"/>
        </svg>
        <span>hello@kovlo.io</span>
      </div>
      <p class="contact__address">58 Harbour Lane<br>Northfield, 30718</p>
    </div>

    <span class="website">www.kovlo.io</span>
  </section>

</body>
</html>
```